Looking for someone to design a business card for my plumbing business Quandor Plumbing Solutions I want the background also to be black, must attract clients. If possible I want the front to be the logo and the back to show maybe the details.

Target Market(s)

Clients

Industry/Entity Type

Plumbing maintenance

Contact Information for Business Card

Name: Felix, Contact: 0461 539 207, Email: quandorplumbingsolutions@mailbrook.example, Licence number 728093K

Font styles to use
Other font styles liked:
• as per logo maybe?

Colors

Designer to choose colors to be used in the design.

Requirements
Nice to have
• stating the service I provide, emergency plumbing, plumbing maintenance, drainage maintenance, block sewer and stormwater, camera and locating.

```html
<!DOCTYPE html>
<html lang="en">
<head>
<meta charset="utf-8">
<title>Quandor Plumbing Solutions – Business Card</title>
<link href="https://fonts.googleapis.com/css2?family=Montserrat:wght@400;500;800&display=swap" rel="stylesheet">
<style>
  :root {
    --stage: #3a3a3a;
    --card: #141414;
    --brand-blue: #4f93d6;
    --ink-light: #f2f2f2;
    --ink-muted: #d9d9d9;
  }
  * { box-sizing: border-box; margin: 0; padding: 0; }
  html, body {
    width: 1200px; height: 689px; overflow: hidden;
    background: var(--stage);
    font-family: "Montserrat", sans-serif;
  }
  .stage {
    width: 1200px; height: 689px;
    display: flex; align-items: center; justify-content: center; gap: 40px;
  }
  .card {
    width: 550px; height: 315px;
    background: var(--card);
    border-radius: 22px;
    box-shadow: 0 18px 40px rgba(0,0,0,.45);
    position: relative;
    overflow: hidden;
  }
  /* Wordmark */
  .wordmark {
    display: flex; align-items: center; gap: 14px;
    color: var(--brand-blue);
    font-weight: 800;
    text-transform: uppercase;
  }
  .wordmark-dot {
    width: 18px; height: 18px; border-radius: 50%;
    background: var(--brand-blue); flex: none;
  }
  .wordmark-name { line-height: 1; }
  .wordmark-name .primary { display: block; letter-spacing: 1px; }
  .wordmark-name .secondary { display: block; letter-spacing: 1.5px; margin-top: 6px; }

  /* Front */
  .card--front { display: flex; align-items: center; justify-content: center; }
  .card--front .wordmark-dot { width: 30px; height: 30px; }
  .card--front .primary { font-size: 52px; }
  .card--front .secondary { font-size: 17.5px; }

  /* Back */
  .card--back { display: flex; align-items: center; padding: 0 26px; }
  .card--back .wordmark { width: 200px; flex: none; gap: 10px; }
  .card--back .wordmark-dot { width: 14px; height: 14px; }
  .card--back .primary { font-size: 28px; }
  .card--back .secondary { font-size: 9.5px; letter-spacing: 0.6px; margin-top: 5px; }
  .divider {
    width: 1.5px; height: 150px; background: var(--brand-blue);
    margin: 0 16px 0 8px; flex: none;
  }
  .details { color: var(--ink-light); }
  .details .name {
    color: var(--brand-blue); font-weight: 800; font-size: 26px; margin-bottom: 10px;
  }
  .details .licence { font-size: 12px; color: var(--ink-muted); margin-bottom: 20px; }
  .contact-line {
    display: flex; align-items: center; gap: 7px;
    font-size: 11px; font-weight: 500; margin-top: 7px; white-space: nowrap;
  }
  .contact-line svg { width: 12px; height: 12px; flex: none; fill: var(--brand-blue); }
</style>
</head>
<body>
  <main class="stage">
    <section class="card card--front" aria-label="Card front">
      <div class="wordmark">
        <span class="wordmark-dot"></span>
        <span class="wordmark-name">
          <span class="primary">Quandor</span>
          <span class="secondary">Plumbing Solutions</span>
        </span>
      </div>
    </section>

    <section class="card card--back" aria-label="Card back">
      <div class="wordmark">
        <span class="wordmark-dot"></span>
        <span class="wordmark-name">
          <span class="primary">Quandor</span>
          <span class="secondary">Plumbing Solutions</span>
        </span>
      </div>
      <span class="divider"></span>
      <div class="details">
        <p class="name">Felix</p>
        <p class="licence">Licence number 728093K</p>
        <p class="contact-line">
          <svg viewBox="0 0 24 24" aria-hidden="true"><path d="M6.6 10.8a15.1 15.1 0 0 0 6.6 6.6l2.2-2.2c.3-.3.7-.4 1-.2 1.1.4 2.3.6 3.6.6.6 0 1 .4 1 1V20c0 .6-.4 1-1 1A17 17 0 0 1 3 4c0-.6.4-1 1-1h3.5c.6 0 1 .4 1 1 0 1.3.2 2.5.6 3.6.1.3 0 .7-.2 1z"/></svg>
          0461 539 207
        </p>
        <p class="contact-line">
          <svg viewBox="0 0 24 24" aria-hidden="true"><path d="M2 5h20v14H2zm2 2v.4l8 5 8-5V7zm0 2.8V17h16V9.8l-8 5z"/></svg>
          quandorplumbingsolutions@mailbrook.example
        </p>
      </div>
    </section>
  </main>
</body>
</html>
```